Business Card for a New Zealand IT Startup

I need a business card for VELTA Holdings. We are a young startup based in New Zealand working in internet marketing and web development. The design should have some element connected to New Zealand, such as wave, koru or silver fern, just don't use a kiwi bird.

```html
<!DOCTYPE html>
<html lang="en">
<head>
<meta charset="utf-8">
<title>VELTA Holdings — Business Card</title>
<link href="https://fonts.googleapis.com/css2?family=Montserrat:wght@500;600;700&family=Open+Sans:wght@400;600&display=swap" rel="stylesheet">
<style>
  :root{
    --bg:#dcdcdc;
    --orange:#f15a24;
    --blue:#0a6ab8;
    --ink:#333a44;
    --navy:#2b3a8c;
    --white:#ffffff;
    --faint:#e3eef8;
  }
  *{box-sizing:border-box;margin:0;padding:0}
  html,body{width:1200px;height:900px;overflow:hidden}
  body{background:radial-gradient(circle at 40% 30%,#ececec,var(--bg));font-family:"Open Sans",sans-serif;position:relative}
  .card{position:absolute;width:540px;height:310px;border-radius:26px;overflow:hidden;box-shadow:0 10px 24px rgba(0,0,0,.18)}
  .card-front{left:70px;top:110px;background:linear-gradient(170deg,var(--orange) 0%,var(--orange) 22%,var(--blue) 62%,var(--blue) 100%);display:flex;align-items:center;justify-content:center}
  .brand-front{font-family:"Montserrat",sans-serif;font-weight:700;font-size:52px;color:var(--white);letter-spacing:3px}
  .card-back{left:590px;top:470px;background:var(--white)}
  .deco-circle{position:absolute;right:40px;top:18px;width:200px;height:200px;border-radius:50%;background:var(--faint)}
  .brand-back{position:absolute;left:34px;top:120px;font-family:"Montserrat",sans-serif;font-weight:700;font-size:34px;color:var(--blue);letter-spacing:2px}
  .person{position:absolute;left:34px;top:172px}
  .person-name{font-family:"Montserrat",sans-serif;font-weight:700;font-size:17px;color:var(--blue);letter-spacing:.5px}
  .person-title{font-size:13px;color:var(--ink);margin-top:1px}
  .contacts{position:absolute;left:34px;top:218px;list-style:none}
  .contacts li{display:flex;align-items:center;gap:7px;font-size:13px;color:var(--ink);line-height:17px}
  .contacts svg{width:10px;height:10px;fill:var(--navy);flex:none}
  .address{position:absolute;right:30px;top:198px;text-align:right;font-size:13px;color:var(--ink);line-height:17px}
  .stripe{position:absolute;bottom:0;left:0;width:100%;height:14px}
</style>
</head>
<body>
  <section class="card card-front">
    <div class="brand-front">VELTA Holdings</div>
  </section>

  <section class="card card-back">
    <div class="deco-circle"></div>
    <div class="brand-back">VELTA Holdings</div>
    <div class="person">
      <p class="person-name">AARON WHITLEY</p>
      <p class="person-title">Managing Director</p>
    </div>
    <ul class="contacts">
      <li><svg viewBox="0 0 10 10"><path d="M2 1l2 2-1 1.2c.6 1.2 1.6 2.2 2.8 2.8L7 6l2 2-1.4 1.4C4.5 9.2.8 5.5.6 2.4z"/></svg>044-123 456 789</li>
      <li><svg viewBox="0 0 10 10"><path d="M2.5 0h5v10h-5zM3.3 1v7h3.4V1z"/></svg>044-123 456 789</li>
      <li><svg viewBox="0 0 10 10"><path d="M0 2h10v6H0zM1 3v.3L5 6l4-2.7V3L5 5.6z"/></svg>hello@veltamail.com</li>
      <li><svg viewBox="0 0 10 10"><circle cx="5" cy="5" r="5"/></svg>www.veltaholdings.com</li>
    </ul>
    <p class="address">12345, Address Goes Here<br>Country Name, 123456</p>
    <svg class="stripe" viewBox="0 0 540 14" preserveAspectRatio="none">
      <polygon points="0,0 330,0 318,14 0,14" fill="var(--blue)"/>
      <polygon points="330,0 540,0 540,14 318,14" fill="var(--orange)"/>
    </svg>
  </section>
</body>
</html>
```